Audio and Video download site

I am looking for a good and beautiful website where users can be a able to download and upload musicial files and video file. Basically, there will be two categories. The first category for the music files( mp3, mva and other popular music files) while the second category will be for video files (mp4, wmv, divx and other files) users would be able to like and dislike a song/video. Users do not necessarily have to sign up for them to make you or download and upload files from the website. The website should be youthful.

```html
<!DOCTYPE html>
<html lang="en">
<head>
<meta charset="utf-8">
<title>TuneDrift – Log In</title>
<link href="https://fonts.googleapis.com/css2?family=Quicksand:wght@300;400;500&display=swap" rel="stylesheet">
<style>
  :root {
    --maroon: #7a0019;
    --white: #ffffff;
    --topbar: rgba(15, 30, 35, 0.85);
    --card: rgba(214, 214, 214, 0.93);
    --field: #8a8a8a;
    --footer: rgba(70, 110, 165, 0.85);
    --glow: 200, 215, 240;
  }
  * { box-sizing: border-box; margin: 0; padding: 0; }
  html, body { width: 1200px; height: 960px; overflow: hidden; }
  body {
    position: relative;
    font-family: "Quicksand", sans-serif;
    font-weight: 300;
    color: var(--white);
    background: #2a2f38;
  }
  .backdrop {
    position: absolute; inset: 0;
    background:
      radial-gradient(ellipse 360px 420px at 600px 640px, #5a4d4c 0%, rgba(90,77,76,0) 70%),
      linear-gradient(180deg, #3c4650 0%, #343c48 40%, #2b3140 70%, #3a4056 100%);
  }
  .topbar {
    position: absolute; top: 0; left: 0; width: 1200px; height: 42px;
    background: var(--topbar);
    display: flex; justify-content: flex-end; align-items: center;
    gap: 42px; padding-right: 10px;
  }
  .topbar a { color: var(--white); text-decoration: none; font-size: 22px; font-weight: 400; }
  .welcome {
    position: absolute; top: 124px; width: 100%; text-align: center;
    font-size: 49px; font-weight: 300; letter-spacing: 1px;
  }
  .tagline {
    position: absolute; top: 226px; width: 100%; text-align: center;
    font-size: 34px; font-weight: 300; letter-spacing: 1.2px;
  }
  .glow-art {
    position: absolute;
    filter: blur(14px);
  }
  .glow-art.headphones {
    left: 159px; top: 401px; width: 300px; height: 321px;
    border-radius: 50%;
    background: radial-gradient(ellipse at 50% 55%, rgba(var(--glow),0.42) 0%, rgba(var(--glow),0.22) 45%, rgba(var(--glow),0) 72%);
  }
  .glow-art.play {
    left: 792px; top: 427px; width: 235px; height: 271px;
    border-radius: 50%;
    background: radial-gradient(ellipse at 35% 50%, rgba(var(--glow),0.45) 0%, rgba(var(--glow),0.2) 45%, rgba(var(--glow),0) 72%);
  }
  .login-card {
    position: absolute; left: 388px; top: 292px; width: 420px; height: 522px;
    background: var(--card); border-radius: 6px;
    box-shadow: 0 2px 8px rgba(0,0,0,0.35);
    color: var(--maroon); text-align: center;
  }
  .login-card h2 { margin-top: 22px; font-size: 35px; font-weight: 400; }
  .field {
    position: absolute; left: 27px; width: 366px; height: 59px;
    background: var(--field);
    border: 3px solid #6f6f6f;
    box-shadow: inset 0 0 8px rgba(0,0,0,0.5);
    font-family: inherit; font-size: 30px; font-weight: 400;
    color: var(--maroon); padding-left: 8px; text-align: left; line-height: 53px;
  }
  .field.username { top: 83px; }
  .field.password { top: 160px; left: 25px; }
  .submit { position: absolute; left: 177px; top: 234px; }
  .prompt { position: absolute; width: 100%; font-size: 25px; font-weight: 400; line-height: 23px; }
  .prompt a { color: var(--maroon); }
  .prompt.register { top: 337px; }
  .prompt.guest { top: 427px; }
  .footer {
    position: absolute; left: 0; top: 902px; width: 1200px; height: 58px;
    background: var(--footer);
    text-align: center; font-size: 12px; font-weight: 500; line-height: 14px; padding-top: 16px;
  }
  .footer a { color: var(--white); }
</style>
</head>
<body>
  <div class="backdrop" role="img" aria-label="Blurred street photo of a listener wearing headphones"></div>

  <nav class="topbar">
    <a href="#">Log In</a>
    <a href="#">Register</a>
  </nav>

  <h1 class="welcome">Welcome to TuneDrift.</h1>
  <p class="tagline">Where do you want us to take you today?</p>

  <div class="glow-art headphones" role="img" aria-label="Glowing headphones illustration"></div>
  <div class="glow-art play" role="img" aria-label="Large glowing play symbol illustration"></div>

  <form class="login-card">
    <h2>Log in to your account</h2>
    <div class="field username">username</div>
    <div class="field password">password</div>
    <svg class="submit" width="66" height="66" viewBox="0 0 66 66" role="img" aria-label="Log in">
      <circle cx="33" cy="33" r="33" fill="#7a0019"/>
      <polygon points="22,15 52,33 22,51" fill="#ffffff"/>
    </svg>
    <p class="prompt register">Don't have an account?<br><a href="#">Register here.</a></p>
    <p class="prompt guest">Want to stay anonymous?<br><a href="#">Sign in as guest.</a></p>
  </form>

  <footer class="footer">
    Copyright © 2016 TuneDrift. Use of this website constitutes acceptance of our<br>
    <a href="#">User Agreement</a> and <a href="#">Privacy Policy</a>.
  </footer>
</body>
</html>
```